Brookvane Consulting Business Card Design

Business Card Design for Brookvane Consulting. Brookvane Consulting is a boutique consultancy based in Atlanta, GA., that specializes in marketing strategy, organization planning, and leadership development. We provide solutions for small businesses and startups as well as Vantage 300 companies.

http://brookvaneconsulting.com/

Target Market(s)

We provide solutions for small businesses and startups as well as Vantage 300 companies.

Industry/Entity Type

Consulting

Contact Information for Business Card

Two sided business card with priority on contact information, logo, tag line (Inspiration to Dream More, Do More, Become More)

Colors

Designer to choose colors to be used in the design.

Requirements
Must have
• contact information, logo, tag line (Inspiration to Dream More, Do More, Become More)
• Simple no over communication.
Nice to have
• I would like to see different placements of logo and creative use of both sides of the card
Should not have
• Do not put too much information on the card.

```html
<!DOCTYPE html>
<html lang="en">
<head>
<meta charset="utf-8">
<title>Brookvane Consulting – Business Card</title>
<link rel="stylesheet" href="https://fonts.googleapis.com/css2?family=Lato:wght@400;700&family=Yellowtail&display=swap">
<style>
  :root {
    --stage: #ecebea;
    --card-dark: #333333;
    --frost-light: #f2efee;
    --frost-mid: #e3dcda;
    --ink: #3a3a3a;
    --ink-faint: #9a9696;
    --text-light: #ffffff;
    --text-muted: #d6d6d6;
  }
  * { margin: 0; padding: 0; box-sizing: border-box; }
  html, body { width: 1200px; height: 900px; overflow: hidden; background: var(--stage); }
  .canvas { position: relative; width: 1200px; height: 900px; font-family: "Lato", Arial, sans-serif; }

  .card {
    position: absolute;
    overflow: hidden;
    box-shadow: 0 6px 18px rgba(0,0,0,0.18);
  }
  .card__bg { position: absolute; inset: 0; width: 100%; height: 100%; display: block; }

  .card--front { left: 78px; top: 35px; width: 588px; height: 362px; }
  .card--back  { left: 388px; top: 505px; width: 567px; height: 352px; }

  .holder { position: absolute; left: 35px; top: 54px; color: var(--text-light); }
  .holder__name { font-weight: 700; font-size: 20px; letter-spacing: 0.2px; line-height: 1.2; }
  .holder__title { font-weight: 400; font-size: 16px; color: var(--text-muted); line-height: 1.2; }

  .contact { position: absolute; left: 37px; top: 262px; list-style: none; color: var(--text-light); font-size: 16px; }
  .contact__item { display: flex; align-items: center; gap: 6px; height: 22px; }
  .contact__icon { width: 13px; height: 13px; fill: var(--text-light); flex: none; }

  .wordmark {
    position: absolute;
    font-family: "Lato", Arial, sans-serif;
    font-weight: 400;
    color: var(--ink);
    text-align: center;
    line-height: 1;
  }
  .wordmark__name { display: block; font-size: 44px; }
  .wordmark__sub { display: block; font-size: 19px; letter-spacing: 3px; margin-top: 10px; }
  .card--front .wordmark { left: 265px; top: 135px; width: 290px; }
  .card--back .wordmark { left: 10px; top: 130px; width: 290px; color: var(--ink-faint); opacity: 0.75; }

  .tagline {
    position: absolute;
    right: 27px;
    top: 225px;
    text-align: right;
    font-family: "Yellowtail", cursive;
    font-size: 26px;
    line-height: 32px;
    color: var(--text-light);
  }
</style>
</head>
<body>
<main class="canvas">

  <section class="card card--front" aria-label="Business card front">
    <svg class="card__bg" viewBox="0 0 588 362" preserveAspectRatio="none" aria-hidden="true">
      <defs>
        <linearGradient id="frostFront" x1="0" y1="0" x2="1" y2="1">
          <stop offset="0" stop-color="var(--frost-light)"/>
          <stop offset="1" stop-color="var(--frost-mid)"/>
        </linearGradient>
      </defs>
      <rect width="588" height="362" fill="var(--card-dark)"/>
      <polygon points="497,0 588,0 588,362 497,362 162,177" fill="url(#frostFront)"/>
    </svg>

    <div class="holder">
      <p class="holder__name">DANIEL WHITMORE</p>
      <p class="holder__title">Managing Director</p>
    </div>

    <div class="wordmark">
      <span class="wordmark__name">Brookvane</span>
      <span class="wordmark__sub">CONSULTING</span>
    </div>

    <ul class="contact">
      <li class="contact__item">
        <svg class="contact__icon" viewBox="0 0 16 16" aria-hidden="true"><path d="M3 2h3l1.5 3.5-2 1.2a8 8 0 0 0 3.8 3.8l1.2-2L14 10v3a1 1 0 0 1-1 1A11 11 0 0 1 2 3a1 1 0 0 1 1-1z"/></svg>
        <span>404 555 0192</span>
      </li>
      <li class="contact__item">
        <svg class="contact__icon" viewBox="0 0 16 16" aria-hidden="true"><path d="M1 3h14v10H1z M2 4l6 5 6-5" fill="none" stroke="var(--text-light)" stroke-width="1.6"/></svg>
        <span>info@brookvaneconsulting.com</span>
      </li>
      <li class="contact__item">
        <svg class="contact__icon" viewBox="0 0 16 16" aria-hidden="true"><circle cx="8" cy="8" r="7"/><path d="M1 8h14M8 1c3 3 3 11 0 14M8 1c-3 3-3 11 0 14" fill="none" stroke="var(--card-dark)" stroke-width="1.1"/></svg>
        <span>www.brookvaneconsulting.com</span>
      </li>
    </ul>
  </section>

  <section class="card card--back" aria-label="Business card back">
    <svg class="card__bg" viewBox="0 0 567 352" preserveAspectRatio="none" aria-hidden="true">
      <defs>
        <linearGradient id="frostBack" x1="0" y1="0" x2="1" y2="1">
          <stop offset="0" stop-color="var(--frost-light)"/>
          <stop offset="1" stop-color="var(--frost-mid)"/>
        </linearGradient>
      </defs>
      <rect width="567" height="352" fill="var(--card-dark)"/>
      <polygon points="0,0 68,0 390,168 64,352 0,352" fill="url(#frostBack)"/>
    </svg>

    <div class="wordmark">
      <span class="wordmark__name">Brookvane</span>
      <span class="wordmark__sub">CONSULTING</span>
    </div>

    <p class="tagline">Inspiration to<br>Dream More<br>Do More, Become More</p>
  </section>

</main>
</body>
</html>
```